Larkfield Ridge Management

I need a professional website. My current website is larkfieldridgemanagement.com and I hate it. It was created with some AI tool very quickly because I needed a site up and running with no advanced notice. I’m open to all designs .. I trust you, the professionals will deliver the results I’m anxiously awaiting! :)

```html
<!DOCTYPE html>
<html lang="en">
<head>
<meta charset="utf-8">
<title>Larkfield Ridge Management</title>
<link href="https://fonts.googleapis.com/css2?family=Outfit:wght@500;600;700;800;900&family=Inter:wght@400;500;600&display=swap" rel="stylesheet">
<style>
:root{
  --navy:#1b2a4e;
  --navy-deep:#172447;
  --red:#c8102e;
  --paper:#f2f2f2;
  --ink:#1d1d1f;
  --white:#ffffff;
  --grey-dark:#3e3f42;
}
*{margin:0;padding:0;box-sizing:border-box}
html,body{width:1200px;height:3365px;overflow:hidden}
body{position:relative;background:var(--paper);font-family:"Inter",Arial,sans-serif;color:var(--ink)}
.abs{position:absolute}
.display{font-family:"Outfit",Arial,sans-serif;font-weight:800;letter-spacing:.2px}
.btn{position:absolute;display:flex;align-items:center;justify-content:space-between;padding:0 24px;background:var(--red);color:var(--white);border-radius:22px;font-family:"Outfit",Arial,sans-serif;font-weight:700;font-size:13px;text-transform:uppercase;text-decoration:none}
.btn svg{width:14px;height:14px}

/* hero */
.hero-photo{left:0;top:0;width:1200px;height:790px;background:linear-gradient(180deg,#8fa8c6 0%,#b7c4cf 16%,#6f8a5a 26%,#7f8b86 45%,#5a6468 75%,#4b5357 100%)}
.brand-mark{left:157px;top:40px;width:160px;color:var(--white);font-family:"Outfit",Arial,sans-serif;font-weight:800;font-size:22px;line-height:1.05;text-transform:uppercase}
.nav{left:731px;top:61px;display:flex;gap:30px;font-size:12px;color:var(--white);text-transform:uppercase;letter-spacing:.3px}
.nav .active{color:var(--red)}
.hero-title{left:0;width:1200px;top:192px;text-align:center;color:var(--white);font-size:76px;line-height:1;text-transform:uppercase}
.hero-title span{color:var(--red)}
.hero-sub{left:0;width:1200px;top:278px;text-align:center;color:var(--white);font-size:42px;text-transform:uppercase}
.hero-cta{left:507px;top:366px;width:186px;height:40px;justify-content:center;font-size:16px}

/* expertise */
.drawing{left:0;top:560px;width:606px;height:537px;background:linear-gradient(180deg,#ececee,#e2e3e6)}
.expertise-brand{left:183px;top:880px;width:320px;color:var(--navy);font-family:"Outfit",Arial,sans-serif;font-weight:800;font-size:44px;line-height:1.05;text-transform:uppercase}
.expertise-title{left:610px;top:840px;color:var(--navy);font-size:38px;line-height:46px;text-transform:uppercase}
.expertise-text{left:610px;top:940px;width:430px;font-size:12.5px;line-height:19px;color:#333}
.expertise-btn{left:610px;top:1016px;width:188px;height:40px}

/* about */
.about-photo{left:0;top:1138px;width:1200px;height:680px;background:linear-gradient(90deg,#58595c,#3c3d40 55%,#46474a)}
.about-title{left:159px;top:1210px;color:var(--white);font-size:38px;line-height:45px;text-transform:uppercase}
.about-text{left:159px;width:430px;font-size:12px;line-height:19px;color:#f1f1f1}
.about-btn{left:159px;top:1558px;width:187px;height:40px}
.about-feature{left:672px;top:1196px;width:392px;height:430px;border-radius:10px;background:linear-gradient(160deg,#8a6f55,#6c6f6a 45%,#7f8790)}

/* services */
.services-title{left:0;width:1200px;top:1866px;text-align:center;color:var(--white);font-size:38px;text-transform:uppercase}
.services-ribbon{left:303px;top:1926px;width:595px;height:46px;background:var(--red);clip-path:polygon(2% 0,98% 0,100% 50%,98% 100%,0 100%,1.5% 50%);display:flex;align-items:center;justify-content:center;color:var(--white);font-family:"Outfit",Arial,sans-serif;font-weight:800;font-size:21px;text-transform:uppercase}
.services-text{left:180px;width:840px;text-align:center;color:#e8ebf2;font-size:12.5px;line-height:19px}
.skyline{left:0;top:2290px;width:1200px;height:191px;background:linear-gradient(180deg,rgba(255,255,255,0),rgba(255,255,255,.05))}
.price-card{top:2125px;width:277px;height:194px;border-radius:8px;padding:18px 28px;color:var(--white);background:#213a6b}
.price-card.featured{background:var(--red)}
.price-card h3{font-family:"Outfit",Arial,sans-serif;font-weight:600;font-size:19px}
.price-card .price{font-family:"Outfit",Arial,sans-serif;font-weight:800;font-size:40px;line-height:1.1;margin:4px 0 6px}
.price-card p{font-size:9.5px;line-height:19px}
.services-btn{left:487px;top:2356px;width:226px;height:40px}

/* proposal */
.proposal-title{left:161px;top:2545px;color:var(--navy);font-size:38px;line-height:46px;text-transform:uppercase}
.proposal-text{left:161px;top:2650px;width:420px;font-size:11.5px;line-height:19px;color:#222}
.proposal-photo{left:161px;top:2707px;width:425px;height:229px;border-radius:12px;background:linear-gradient(180deg,#7a88a3 0%,#6b4a3e 40%,#3a2a24 100%)}
.field-label{left:681px;font-size:15px;color:#222}
.field{left:680px;width:361px;height:40px;border:1.5px solid var(--navy);border-radius:4px;background:var(--white)}
.send-btn{left:679px;top:2916px;width:113px;height:40px;padding:0 18px}

/* footer */
.footer-brand{left:519px;top:3058px;width:162px;text-align:center;color:var(--white);font-family:"Outfit",Arial,sans-serif;font-weight:800;font-size:19px;line-height:1.1;text-transform:uppercase}
.footer-link{top:3112px;color:var(--white);font-size:15px}
.footer-link.active{color:var(--red)}
.contact-icon{width:38px;height:38px;border-radius:50%;background:var(--red);display:flex;align-items:center;justify-content:center}
.contact-icon svg{width:17px;height:17px;fill:var(--white)}
.contact-text{top:3196px;color:var(--white);font-size:16px}
.footer-rule{left:0;top:3258px;width:1200px;height:1px;background:rgba(255,255,255,.35)}
.copyright{left:0;width:1200px;top:3290px;text-align:center;color:var(--white);font-size:16px}
</style>
</head>
<body>

<!-- hero -->
<div class="abs hero-photo" role="img" aria-label="Aerial view of a suburban housing development with mountains on the horizon"></div>
<div class="abs brand-mark">Larkfield Ridge Management</div>
<nav class="abs nav"><span class="active">Home</span><span>About</span><span>Services</span><span>Contact Us</span></nav>
<h1 class="abs display hero-title">A <span>True</span> Partner</h1>
<div class="abs display hero-sub">Not just a vendor.</div>
<a class="btn hero-cta">Get in touch</a>

<svg class="abs" style="left:0;top:318px" width="56" height="64" viewBox="0 0 56 64"><polygon points="0,0 56,32 0,64" fill="var(--navy)"/><polyline points="22,25 15,32 22,39" fill="none" stroke="#fff" stroke-width="3"/></svg>
<svg class="abs" style="left:1144px;top:318px" width="56" height="64" viewBox="0 0 56 64"><polygon points="56,0 0,32 56,64" fill="var(--red)"/><polyline points="34,25 41,32 34,39" fill="none" stroke="#fff" stroke-width="3"/></svg>

<!-- expertise -->
<div class="abs drawing" role="img" aria-label="Light architectural line drawing of an apartment building"></div>
<svg class="abs" style="left:0;top:540px" width="1200" height="250" viewBox="0 0 1200 250">
  <polygon points="0,8 600,237 1200,8 1200,250 0,250" fill="var(--paper)"/>
  <polygon points="0,8 600,237 606,237 606,250 0,250" fill="#e6e7ea"/>
  <polygon points="444,159 757,159 600,230" fill="var(--red)"/>
</svg>
<div class="abs expertise-brand">Larkfield Ridge Management</div>
<h2 class="abs display expertise-title">Expertise rooted in<br>asset preservation</h2>
<p class="abs expertise-text">The organization applies rigorously tested frameworks and data-driven methodologies to safeguard property value while elevating tenant experience.</p>
<a class="btn expertise-btn">Learn more <svg viewBox="0 0 14 14"><path d="M1 7h11M8 3l4 4-4 4" fill="none" stroke="#fff" stroke-width="1.8"/></svg></a>

<!-- about -->
<div class="abs about-photo" role="img" aria-label="Muted photo of modern apartment buildings"></div>
<svg class="abs" style="left:0;top:1590px" width="1200" height="230" viewBox="0 0 1200 230">
  <polygon points="0,16 600,199 1200,16 1200,230 0,230" fill="#fff"/>
  <polygon points="0,36 600,219 1200,36 1200,230 0,230" fill="var(--navy)"/>
</svg>
<h2 class="abs display about-title">About our property<br>management<br>solutions</h2>
<p class="abs about-text" style="top:1366px">Our organization delivers comprehensive property management solutions that optimize asset performance and tenant satisfaction. By integrating advanced analytics with proven operational frameworks, our specialists ensure each property achieves sustained value appreciation.</p>
<p class="abs about-text" style="top:1460px">Drawing on decades of collective expertise, the team facilitates regulatory compliance, cost efficiency, and proactive maintenance. This disciplined approach enables owners to preserve capital, enhance occupancy rates, and demonstrate long-term resilience across diverse market conditions.</p>
<a class="btn about-btn">Learn more <svg viewBox="0 0 14 14"><path d="M1 7h11M8 3l4 4-4 4" fill="none" stroke="#fff" stroke-width="1.8"/></svg></a>
<div class="abs about-feature" role="img" aria-label="Two people shaking hands with a property manager outside a modern home"></div>

<!-- services -->
<div class="abs" style="left:0;top:1818px;width:1200px;height:663px;background:var(--navy)"></div>
<div class="abs skyline" role="img" aria-label="Faint outline illustration of a row of houses"></div>
<h2 class="abs display services-title">Services</h2>
<div class="abs services-ribbon">Strategic property management solutions</div>
<p class="abs services-text" style="top:1991px">Our analysis demonstrates that effective property oversight originates from meticulous operational planning, transparent communication channels, and data-driven performance metrics across every asset class.</p>
<p class="abs services-text" style="top:2047px">By integrating advanced technology with industry expertise, our team implements proactive maintenance schedules that preserve asset value and facilitate sustainable, long-term returns for stakeholders.</p>

<div class="abs price-card" style="left:159px"><h3>Basic Service</h3><div class="price">$99</div><p>Describe important details like price, value, length of service, and why it's unique. Or use these sections to showcase different key values of your products or services.</p></div>
<div class="abs price-card featured" style="left:462px"><h3>Intermediate Service</h3><div class="price">$149</div><p>Describe important details like price, value, length of service, and why it's unique. Or use these sections to showcase different key values of your products or services.</p></div>
<div class="abs price-card" style="left:761px"><h3>Advanced Service</h3><div class="price">$199</div><p>Describe important details like price, value, length of service, and why it's unique. Or use these sections to showcase different key values of your products or services.</p></div>
<a class="btn services-btn">Advanced+ Service <svg viewBox="0 0 14 14"><path d="M1 7h11M8 3l4 4-4 4" fill="none" stroke="#fff" stroke-width="1.8"/></svg></a>

<!-- proposal -->
<h2 class="abs display proposal-title">Request a<br>tailored proposal</h2>
<p class="abs proposal-text">Submit the form to initiate a consultative assessment and explore solutions aligned with your objectives.</p>
<div class="abs proposal-photo" role="img" aria-label="Modern townhouses lit at dusk"></div>

<label class="abs field-label" style="top:2565px">First Name</label><div class="abs field" style="top:2591px"></div>
<label class="abs field-label" style="top:2642px">Last Name</label><div class="abs field" style="top:2667px"></div>
<label class="abs field-label" style="top:2718px">Email</label><div class="abs field" style="top:2743px"></div>
<label class="abs field-label" style="top:2794px">Message</label><div class="abs field" style="top:2818px;height:84px"></div>
<a class="btn send-btn">Send <svg viewBox="0 0 14 14"><path d="M1 7h11M8 3l4 4-4 4" fill="none" stroke="#fff" stroke-width="1.8"/></svg></a>

<!-- footer -->
<svg class="abs" style="left:0;top:2912px" width="1200" height="453" viewBox="0 0 1200 453">
  <polygon points="0,0 600,108 1200,0 1200,453 0,453" fill="var(--navy)"/>
</svg>
<div class="abs footer-brand">Larkfield Ridge Management</div>
<span class="abs footer-link active" style="left:357px">Home</span>
<span class="abs footer-link" style="left:439px">About</span>
<span class="abs footer-link" style="left:717px;top:3116px">Services</span>
<span class="abs footer-link" style="left:816px;top:3116px">Contact Us</span>

<div class="abs contact-icon" style="left:157px;top:3188px"><svg viewBox="0 0 24 24"><path d="M12 2a7 7 0 0 0-7 7c0 5 7 13 7 13s7-8 7-13a7 7 0 0 0-7-7zm0 9.5A2.5 2.5 0 1 1 12 6.5a2.5 2.5 0 0 1 0 5z"/></svg></div>
<span class="abs contact-text" style="left:215px">#123,Lorium ipsum dolor amit, City.</span>
<div class="abs contact-icon" style="left:506px;top:3188px"><svg viewBox="0 0 24 24"><path d="M6.6 10.8a15 15 0 0 0 6.6 6.6l2.2-2.2a1 1 0 0 1 1-.25 11.4 11.4 0 0 0 3.6.57 1 1 0 0 1 1 1V20a1 1 0 0 1-1 1A17 17 0 0 1 3 4a1 1 0 0 1 1-1h3.5a1 1 0 0 1 1 1c0 1.25.2 2.45.57 3.6a1 1 0 0 1-.25 1z"/></svg></div>
<span class="abs contact-text" style="left:563px">1-800 555 0142</span>
<div class="abs contact-icon" style="left:697px;top:3188px"><svg viewBox="0 0 24 24"><path d="M3 5h18a1 1 0 0 1 1 1v12a1 1 0 0 1-1 1H3a1 1 0 0 1-1-1V6a1 1 0 0 1 1-1zm9 7.5L4 7.4V9l8 5 8-5V7.4z"/></svg></div>
<span class="abs contact-text" style="left:754px">info@larkfieldridgemanagement.com</span>
<div class="abs footer-rule"></div>
<div class="abs copyright">© 2026 | www.larkfieldridgemanagement.com</div>

</body>
</html>
```